New Bicycle shop business card

Hi!
I'm looking for a business card for my new proffesional bike mechanics shop. This shop is only for fixing broken bikes and not selling bikes.
Peferbly a modern and sleek and modern design.
Colors: black, grey, red, white
Information:
Name: Rijwielwerkplaats Vanhoutte
Shop owner: Bart Vanhoutte & Marieke Segers
Website: www.rijwielwerkplaats-vanhoutte.be
Email: info@rijwielwerkplaats-vanhoutte.be
Phone number: +32471902368
Street adres: Kerkweg 46
9940 Bellebeke
Slogan/shop information: Herstellingen van alle merken.
Logo: see files.
Target Market(s)
People who seek a mechanic to fix or upgrade their bikes.
Contact Information for Business Card
Information:
Website: info@rijwielwerkplaats-vanhoutte.be
9940 Bellebeke
Logo: see files.

```html
<!DOCTYPE html>
<html lang="nl">
<head>
<meta charset="utf-8">
<title>Rijwielwerkplaats Vanhoutte – visitekaartje</title>
<link href="https://fonts.googleapis.com/css2?family=Montserrat:wght@400;500;700&display=swap" rel="stylesheet">
<style>
  :root {
    --red: #e01f40;
    --white: #ffffff;
    --grey: #a9a9a9;
    --grey-dark: #2b2b2b;
    --ink: #1b1b1b;
  }
  * { box-sizing: border-box; margin: 0; padding: 0; }
  html, body { width: 1200px; height: 880px; overflow: hidden; }
  body {
    background: var(--grey-dark);
    font-family: "Montserrat", Arial, sans-serif;
    position: relative;
  }
  .card {
    position: absolute;
    width: 560px;
    height: 320px;
    border-radius: 22px;
    overflow: hidden;
    box-shadow: 0 18px 40px rgba(0,0,0,.45);
  }

  /* front */
  .card-front {
    left: 60px; top: 100px;
    background: var(--red);
    color: var(--white);
    display: flex; flex-direction: column; align-items: center; justify-content: center;
    text-align: center;
  }
  .brand-mark {
    width: 46px; height: 46px;
    background: var(--white);
    border-radius: 50%;
    margin-bottom: 18px;
  }
  .brand-name {
    font-weight: 700;
    font-size: 28px;
    letter-spacing: 2px;
    line-height: 1.2;
    text-transform: uppercase;
  }
  .brand-name span { display: block; letter-spacing: 11px; font-size: 22px; }
  .slogan {
    margin-top: 14px;
    font-size: 15px;
    letter-spacing: 1.5px;
    font-weight: 400;
  }

  /* back */
  .card-back {
    left: 580px; top: 460px;
    background: var(--white);
  }
  .info-band {
    position: absolute;
    left: 190px; right: 0; top: 78px; height: 176px;
    background: var(--red);
    color: var(--white);
    padding: 16px 20px 0 26px;
  }
  .rule {
    position: absolute; left: 190px; right: 0; height: 2px;
    background: var(--grey);
  }
  .rule-top { top: 70px; }
  .rule-bottom { top: 262px; }
  .owners {
    font-weight: 700;
    font-size: 15px;
    text-transform: uppercase;
    letter-spacing: .2px;
    margin-bottom: 12px;
  }
  .contact-list { list-style: none; }
  .contact-list li {
    display: flex; align-items: center; gap: 10px;
    font-size: 12.5px; line-height: 1; margin-bottom: 9px;
  }
  .contact-icon {
    flex: none; width: 18px; height: 18px; border-radius: 50%;
    background: var(--white);
    display: flex; align-items: center; justify-content: center;
  }
  .contact-icon svg { width: 11px; height: 11px; fill: var(--red); }
  .back-brand {
    position: absolute;
    left: 20px; top: 112px; width: 156px;
    display: flex; flex-direction: column; align-items: flex-start; gap: 10px;
    color: var(--red);
    font-weight: 700; font-size: 11px; line-height: 1.3;
    text-transform: uppercase;
  }
  .back-brand .brand-square {
    flex: none; width: 40px; height: 40px; background: var(--red);
  }
</style>
</head>
<body>

<section class="card card-front">
  <div class="brand-mark"></div>
  <h1 class="brand-name">Rijwielwerkplaats<span>Vanhoutte</span></h1>
  <p class="slogan">Herstellingen Van Alle Merken</p>
</section>

<section class="card card-back">
  <div class="back-brand">
    <div class="brand-square"></div>
    <p>Rijwielwerkplaats<br>Vanhoutte</p>
  </div>
  <div class="rule rule-top"></div>
  <div class="info-band">
    <p class="owners">Bart Vanhoutte &amp; Marieke Segers</p>
    <ul class="contact-list">
      <li><span class="contact-icon"><svg viewBox="0 0 24 24"><path d="M6.6 10.8a15 15 0 0 0 6.6 6.6l2.2-2.2c.3-.3.7-.4 1-.2 1.1.4 2.3.6 3.6.6.6 0 1 .4 1 1V20c0 .6-.4 1-1 1C10.6 21 3 13.4 3 4c0-.6.4-1 1-1h3.5c.6 0 1 .4 1 1 0 1.3.2 2.5.6 3.6.1.3 0 .7-.2 1z"/></svg></span>+32471902368</li>
      <li><span class="contact-icon"><svg viewBox="0 0 24 24"><path d="M2 5h20v14H2zm2 2v.5l8 5 8-5V7l-8 5z"/></svg></span>info@rijwielwerkplaats-vanhoutte.be</li>
      <li><span class="contact-icon"><svg viewBox="0 0 24 24"><path d="M12 2a10 10 0 1 0 0 20 10 10 0 0 0 0-20zm0 2c.9 1.2 1.7 3 2 5h-4c.3-2 1.1-3.8 2-5zM4.3 11h3.7c0 .7 0 1.3.1 2H4.3a8 8 0 0 1 0-2zm5.7 0h4a16 16 0 0 1 0 2h-4a16 16 0 0 1 0-2zm6 0h3.7a8 8 0 0 1 0 2H16c.1-.7.1-1.3 0-2zM10 15h4c-.3 2-1.1 3.8-2 5-.9-1.2-1.7-3-2-5z"/></svg></span>www.rijwielwerkplaats-vanhoutte.be</li>
      <li><span class="contact-icon"><svg viewBox="0 0 24 24"><path d="M12 2a7 7 0 0 0-7 7c0 5 7 13 7 13s7-8 7-13a7 7 0 0 0-7-7zm0 9.5a2.5 2.5 0 1 1 0-5 2.5 2.5 0 0 1 0 5z"/></svg></span>Kerkweg 46, 9940 Bellebeke</li>
    </ul>
  </div>
  <div class="rule rule-bottom"></div>
</section>

</body>
</html>
```